Custom hot rod builder needs a website for launch of new business where he will build luxury garages

We need a website that gives a WOW first impression for "Summit Carports". This is a new business so photos are renderings but we need it to really attract a particular audience. Our initial business is custom hot rods so now we are building garages for them. These will be like luxury "homes" for cars! I will attach our new logo. Website needs to feel powerful and prestigious.

Target Market(s)

middle aged men, car enthusiasts

Industry/Entity Type

automotive, construction

Coding

Coded - Design and coding required

Number of Pages Required

2 page

Font styles to use
Serif

Colors
0054AA
0677BA
7BADD7
CADEEF
E8F1F8

Requirements
Must have
• a WOW factor. luxury. contact form.
Nice to have
• ?

```html
<!DOCTYPE html>
<html lang="en">
<head>
<meta charset="utf-8">
<title>Summit Carports</title>
<link rel="stylesheet" href="https://fonts.googleapis.com/css2?family=Montserrat:wght@500;600;700;800&family=Lato:wght@400;700&display=swap">
<style>
:root{
  --blue:#0054AA;
  --blue-mid:#0677BA;
  --blue-soft:#7BADD7;
  --blue-pale:#CADEEF;
  --blue-mist:#E8F1F8;
  --navy:#063a78;
  --ink:#1b1b1b;
  --text:#444;
  --white:#fff;
  --footer:#1c1c1e;
}
*{box-sizing:border-box;margin:0;padding:0}
html,body{width:1200px;height:4150px;overflow:hidden}
body{font-family:'Lato',sans-serif;color:var(--text);background:var(--white);position:relative}
.section{position:relative;width:1200px;overflow:hidden}
.abs{position:absolute}
h2.section-title{position:absolute;left:0;right:0;text-align:center;font-family:'Montserrat',sans-serif;font-weight:800;font-size:33px;color:var(--ink);letter-spacing:.3px}
.pill{display:inline-flex;align-items:center;justify-content:center;gap:10px;border-radius:40px;font-family:'Montserrat',sans-serif;font-weight:700;color:var(--white);text-decoration:none}
.dot-arrow{width:14px;height:14px;border-radius:50%;background:var(--white);display:inline-block;position:relative}
.dot-arrow::after{content:"";position:absolute;left:5px;top:4px;border-left:5px solid var(--blue);border-top:3px solid transparent;border-bottom:3px solid transparent}

/* social placeholders: plain circle with a centred dot */
.soc{display:flex;align-items:center;justify-content:center;border-radius:50%}
.soc::after{content:"";width:7px;height:7px;border-radius:50%;background:var(--white)}

/* header */
.topbar{height:86px}
.brand{left:111px;top:24px;display:flex;align-items:center;gap:10px;font-family:'Montserrat',sans-serif;font-weight:800;font-size:24px;color:var(--blue)}
.brand .mark{width:34px;height:34px;border-radius:50%;background:var(--blue)}
.contact-chip{display:flex;align-items:center;gap:14px;top:20px}
.contact-chip .ring{width:48px;height:48px;border-radius:50%;border:2px solid var(--blue);display:flex;align-items:center;justify-content:center}
.contact-chip strong{display:block;font-family:'Montserrat',sans-serif;font-size:14px;color:var(--ink)}
.contact-chip span{font-size:15px;color:#333}
.signup{left:960px;top:21px;width:129px;height:44px;background:var(--blue);font-size:15px}
.navbar{height:52px;background:var(--blue)}
.nav-item{top:0;height:52px;line-height:52px;font-family:'Montserrat',sans-serif;font-weight:500;font-size:15px;color:var(--white)}
.nav-item.active{background:var(--navy);padding:0 24px;font-weight:700}
.social{top:12px;display:flex;gap:10px}
.social .soc{width:28px;height:28px;background:var(--navy);border:1px solid rgba(255,255,255,.45)}

/* hero */
.hero{height:644px}
.hero-photo{inset:0;background:linear-gradient(180deg,#8e9fb1 0%,#c3ccd5 22%,#9aa3ab 38%,#5d666f 50%,#3b3f44 60%,#6e7a6a 66%,#b7b8b4 76%,#d8d8d4 100%)}
.hero-title{left:0;right:0;text-align:center;color:var(--white);font-family:'Montserrat',sans-serif;font-weight:800;text-shadow:0 2px 8px rgba(0,0,0,.45)}
.hero-cta{left:523px;top:388px;width:174px;height:50px;background:var(--blue);font-size:15px}
.hero-arrow{top:314px;width:44px;height:44px;border-radius:50%;background:var(--white);border:3px solid rgba(255,255,255,.6);box-shadow:0 0 0 2px rgba(0,0,0,.15)}

/* how it works */
.how{height:692px;background:linear-gradient(180deg,#ffffff 0%,var(--blue-mist) 8%,#f3f6f9 60%,#e9edf1 100%)}
.step{width:200px;font-size:15px;line-height:26px;color:#333}
.step b{display:block;font-weight:700;color:var(--ink)}
.step.left{left:164px;text-align:right}
.step.right{left:836px}

/* about */
.about{height:567px;background:linear-gradient(120deg,#0a4fa3 0%,var(--blue) 50%,#0a5cb3 100%)}
.about h2{left:111px;top:85px;font-family:'Montserrat',sans-serif;font-weight:800;font-size:33px;color:var(--white)}
.about p{left:111px;top:140px;width:455px;font-size:15.5px;line-height:28.3px;color:var(--blue-pale)}
.learn{left:111px;top:420px;width:176px;height:54px;border:2px solid var(--white);font-size:14px}
.frame{left:651px;top:127px;width:383px;height:353px;border:2px solid var(--blue-soft)}
.photo{border:3px solid var(--white)}

/* services */
.services{height:588px}
.card{top:147px;width:309px;text-align:center}
.card .photo-fill{height:203px}
.card h3{margin-top:22px;font-family:'Montserrat',sans-serif;font-weight:700;font-size:14px;color:var(--ink)}
.card p{margin-top:12px;font-size:14.5px;line-height:26px;color:#444;padding:0 20px}
.card a{display:inline-block;margin-top:6px;font-size:15px;color:var(--blue);text-decoration:underline}

/* newsletter */
.newsletter{height:355px}
.news-bg{inset:0;background:linear-gradient(100deg,#6f7c88 0%,#4d6785 28%,#255fa6 52%,var(--blue) 100%)}
.news-car{left:60px;top:160px;width:460px;height:185px;border-radius:38% 42% 14% 14%;background:linear-gradient(90deg,#2a2b5e,#3f3a86 35%,#d98a2e 58%,#3a3580 80%,#25264f)}
.newsletter h2{right:111px;top:80px;white-space:nowrap;text-align:right;font-family:'Montserrat',sans-serif;font-weight:800;font-size:33px;color:var(--white)}
.newsletter p{left:526px;top:134px;width:563px;text-align:center;font-size:14.5px;line-height:25px;color:var(--blue-pale)}
.email-field{left:596px;top:214px;width:292px;height:52px;border-radius:30px;background:var(--white);padding-left:24px;line-height:52px;font-size:14.5px;color:#555}
.submit{left:897px;top:214px;width:139px;height:52px;background:var(--blue);border:2px solid var(--white);font-size:15px}

/* blog */
.blog{height:749px}
.feature{left:126px;top:151px;width:407px;height:509px;background:var(--white);box-shadow:0 2px 12px rgba(0,0,0,.12)}
.feature .photo-fill{height:243px}
.meta{display:flex;gap:24px;font-size:14.5px;color:var(--blue);align-items:center}
.meta span{display:flex;align-items:center;gap:7px}
.meta i{width:12px;height:11px;background:var(--blue);border-radius:2px;display:block}
.post-title{font-family:'Montserrat',sans-serif;font-weight:700;font-size:12.5px;line-height:22px;color:var(--ink)}
.feature .body{font-size:14px;line-height:25.5px;color:#666}
.read{left:21px;top:441px;width:138px;height:44px;background:var(--blue);font-size:15px}
.mini{width:242px}
.mini .photo-fill{height:150px}
.mini .meta{margin-top:14px}
.mini .post-title{margin-top:4px;padding-bottom:6px;border-bottom:2px solid #aaa}

/* footer */
.footer{height:417px;background:var(--footer);color:#ddd}
.foot-brand{left:111px;top:150px;display:flex;align-items:center;gap:12px;font-family:'Montserrat',sans-serif;font-weight:800;font-size:26px;color:var(--white)}
.foot-brand .mark{width:40px;height:40px;border-radius:50%;background:var(--blue-mid)}
.foot-social{left:111px;top:277px;display:flex;gap:8px}
.foot-social .soc{width:35px;height:35px;border:2px solid var(--white)}
.foot-head{top:68px;font-family:'Montserrat',sans-serif;font-weight:700;font-size:14px;color:var(--white)}
.foot-links{top:104px;list-style:none}
.foot-links li{height:38.6px;font-size:15px;color:#e5e5e5;padding-left:26px;position:relative}
.foot-links li::before{content:"»";position:absolute;left:0;top:-2px;color:var(--white);font-size:16px}
.foot-contact{left:868px;display:flex;gap:18px;align-items:flex-start}
.foot-contact .ico{width:30px;height:30px;border-radius:50%;background:#2e2e31;display:flex;align-items:center;justify-content:center;flex:none;margin-top:6px}
.foot-contact b{display:block;font-size:12px;color:var(--white);font-family:'Montserrat',sans-serif}
.foot-contact span{font-size:14.5px;line-height:23px;color:#e5e5e5}
.foot-rule{left:111px;top:346px;width:978px;height:1px;background:#555}
.copy{left:0;right:0;top:371px;text-align:center;font-size:13px;color:#ddd}
</style>
</head>
<body>

<header class="section topbar">
  <div class="abs brand"><span class="mark"></span>Summit Carports</div>
  <div class="abs contact-chip" style="left:460px">
    <div class="ring"><svg width="22" height="22" viewBox="0 0 24 24"><path d="M6.6 10.8a15 15 0 0 0 6.6 6.6l2.2-2.2a1 1 0 0 1 1-.25 11.4 11.4 0 0 0 3.6.57 1 1 0 0 1 1 1V20a1 1 0 0 1-1 1A17 17 0 0 1 3 4a1 1 0 0 1 1-1h3.5a1 1 0 0 1 1 1c0 1.25.2 2.45.57 3.57a1 1 0 0 1-.25 1z" fill="none" stroke="#0054AA" stroke-width="1.6"/></svg></div>
    <div><strong>Call Now:</strong><span>+1 888 888 8888</span></div>
  </div>
  <div class="abs contact-chip" style="left:690px">
    <div class="ring"><svg width="22" height="22" viewBox="0 0 24 24"><rect x="3" y="6" width="18" height="13" rx="2" fill="none" stroke="#0054AA" stroke-width="1.6"/><path d="M3 7l9 6 9-6" fill="none" stroke="#0054AA" stroke-width="1.6"/></svg></div>
    <div><strong>Email Us:</strong><span>info@summitcarports.com</span></div>
  </div>
  <a class="abs pill signup">SIGN UP <svg width="12" height="14" viewBox="0 0 12 14"><circle cx="6" cy="4" r="3.2" fill="#fff"/><path d="M0 14a6 5 0 0 1 12 0z" fill="#fff"/></svg></a>
</header>

<nav class="section navbar">
  <span class="abs nav-item active" style="left:111px">HOME</span>
  <span class="abs nav-item" style="left:241px">ABOUT US</span>
  <span class="abs nav-item" style="left:356px">SERVICES</span>
  <span class="abs nav-item" style="left:467px">HOW ITS&nbsp; WORK</span>
  <span class="abs nav-item" style="left:625px">BLOG</span>
  <span class="abs nav-item" style="left:707px">CONTACT US</span>
  <div class="abs social" style="left:941px" aria-label="Social links"><span class="soc"></span><span class="soc"></span><span class="soc"></span><span class="soc"></span></div>
</nav>

<section class="section hero">
  <div class="abs hero-photo" role="img" aria-label="Rendering of a modern luxury garage with glass front, classic cars inside, palm trees and a paved forecourt"></div>
  <div class="abs hero-title" style="top:218px;font-size:45px">WELCOME TO</div>
  <div class="abs hero-title" style="top:285px;font-size:60px">SUMMIT CARPORTS</div>
  <a class="abs pill hero-cta">GET STARTED <span class="dot-arrow"></span></a>
  <div class="abs hero-arrow" style="left:38px"><svg width="38" height="38" viewBox="0 0 38 38"><path d="M21 13l-6 6 6 6" fill="none" stroke="#333" stroke-width="1.8"/></svg></div>
  <div class="abs hero-arrow" style="left:1118px"><svg width="38" height="38" viewBox="0 0 38 38"><path d="M17 13l6 6-6 6" fill="none" stroke="#333" stroke-width="1.8"/></svg></div>
</section>

<section class="section how">
  <h2 class="section-title" style="top:88px">HOW ITS WORK</h2>

  <div class="abs step left" style="top:181px"><b>Lorem ipsum dolor amet</b>Lorem ipsum dolor sit ameted consectetur adipiscing sed do eiusmod tempor incididunt ut</div>
  <div class="abs step left" style="top:359px"><b>Lorem ipsum dolor amet</b>Lorem ipsum dolor sit ameted consectetur adipiscing sed do eiusmod tempor incididunt ut</div>
  <div class="abs step left" style="top:512px"><b>Lorem ipsum dolor amet</b>Lorem ipsum dolor sit ameted consectetur adipiscing sed do eiusmod tempor incididunt ut</div>
  <div class="abs step right" style="top:181px"><b>Lorem ipsum dolor amet</b>Lorem ipsum dolor sit ameted consectetur adipiscing sed do eiusmod tempor incididunt ut</div>
  <div class="abs step right" style="top:359px"><b>Lorem ipsum dolor amet</b>Lorem ipsum dolor sit ameted consectetur adipiscing sed do eiusmod tempor incididunt ut</div>
  <div class="abs step right" style="top:512px"><b>Lorem ipsum dolor amet</b>Lorem ipsum dolor sit ameted consectetur adipiscing sed do eiusmod tempor incididunt ut</div>

  <svg class="abs" style="left:0;top:0" width="1200" height="692" viewBox="0 0 1200 692" aria-label="Six-step process wheel">
    <defs><clipPath id="wheel"><circle cx="600" cy="405" r="180"/></clipPath></defs>
    <g fill="none" stroke="#0054AA" stroke-width="2">
      <path d="M498 258V225H388"/><path d="M416 410H388"/><path d="M498 540V576H388"/>
      <path d="M702 258V225H812"/><path d="M784 410H812"/><path d="M702 540V576H812"/>
    </g>
    <g fill="#0054AA">
      <path d="M380 225l12-6v12z"/><path d="M380 410l12-6v12z"/><path d="M380 576l12-6v12z"/>
      <path d="M820 225l-12-6v12z"/><path d="M820 410l-12-6v12z"/><path d="M820 576l-12-6v12z"/>
    </g>
    <circle cx="600" cy="405" r="188" fill="none" stroke="#7BADD7" stroke-width="2" stroke-dasharray="4 3"/>
    <circle cx="600" cy="405" r="180" fill="#0054AA"/>
    <rect x="410" y="341" width="380" height="128" fill="#0677BA" clip-path="url(#wheel)"/>
    <line x1="600" y1="220" x2="600" y2="590" stroke="#fff" stroke-width="4"/>
    <circle cx="600" cy="405" r="74" fill="#fff"/>
    <circle cx="600" cy="405" r="80" fill="none" stroke="#fff" stroke-width="3"/>
    <text x="600" y="402" text-anchor="middle" font-family="Montserrat, sans-serif" font-weight="800" font-size="17" fill="#0054AA">SUMMIT</text>
    <text x="600" y="422" text-anchor="middle" font-family="Montserrat, sans-serif" font-weight="800" font-size="13" fill="#0054AA">CARPORTS</text>
    <g fill="none" stroke="#fff" stroke-width="3" stroke-linejoin="round">
      <path d="M508 305v-30h44v30M512 283h36M512 291h36M512 299h36"/>
      <path d="M652 308v-12l8-14h28l8 14v12M652 298h44"/>
      <path d="M452 420v-26h36v26M458 402h24M458 412h24M452 382l10 6M488 382l-10 6"/>
      <path d="M706 424v-26l24-14 24 14v26M716 424v-12l5-8h18l5 8v12"/>
      <path d="M516 530v-10l7-12h26l7 12v10M516 522h40M556 496l4-6M562 502l6-2"/>
      <path d="M640 530h60M644 530v-10l6-8h18l6 8v10M678 530v-20l12-10 12 10v20"/>
    </g>
  </svg>
</section>

<section class="section about">
  <h2 class="abs">ABOUT US</h2>
  <p class="abs">Lorem ipsum dolor sit amet, consectetur adipiscing elited sed did eiusmod tempor incididunt ut labore etet dolore magna aliquateid enim ad minim veniam, quis nostrud exercitation ullamco laboris nisi ut aliquip ex ea commodo consequat. Duis aute irure dolor in reprehenderit in voluptate velit esse cillum dolore eu fugiat nullat pariatur. Excepteur sint occaecat cupidatat non proident sunt in culpa qui officia deserunt mollit anim&nbsp; est laborum.Excepteur sint occaecat cupidatat non proident sunt in culpa qui officia deserunt mollit anim id est anim&nbsp; est laborum laborum.</p>
  <a class="abs pill learn">LEARN MORE <span class="dot-arrow"></span></a>
  <div class="abs frame"></div>
  <div class="abs photo" style="left:709px;top:61px;width:370px;height:205px;background:linear-gradient(165deg,#9a9ca2,#cfd1d4 40%,#a8423f 70%,#5a5d62)" role="img" aria-label="Mechanic working under the hood of a car in a workshop"></div>
  <div class="abs photo" style="left:615px;top:267px;width:373px;height:237px;background:linear-gradient(170deg,#7a5a44,#b8b0a4 40%,#c8252c 65%,#6b6d70)" role="img" aria-label="Red classic convertible parked inside a brick showroom garage"></div>
</section>

<section class="section services">
  <h2 class="section-title" style="top:79px">OUR SERVICES</h2>
  <div class="abs card" style="left:111px">
    <div class="photo-fill" style="background:linear-gradient(180deg,#b9bec6,#e4e6ea 50%,#9a9ea6)" role="img" aria-label="Cars raised on lifts in a bright service garage"></div>
    <h3>LOREM IPSUM DOLOR SIT AME</h3>
    <p>Lorem ipsum dolor sit amet consectetur adipiscing elit sed doied eiusmod tempor incididunt ut labore et dolore magna .</p>
    <a>Read More</a>
  </div>
  <div class="abs card" style="left:446px">
    <div class="photo-fill" style="background:linear-gradient(180deg,#7a4a22,#b07a40 45%,#3e5a58 75%,#2c2a28)" role="img" aria-label="Classic cars displayed in a warm-lit collector's garage"></div>
    <h3>LOREM IPSUM DOLOR SIT AME</h3>
    <p>Lorem ipsum dolor sit amet consectetur adipiscing elit sed doied eiusmod tempor incididunt ut labore et dolore magna .</p>
    <a>Read More</a>
  </div>
  <div class="abs card" style="left:780px">
    <div class="photo-fill" style="background:linear-gradient(180deg,#5a3c2a,#8a6a50 40%,#c8202a 70%,#3a3a3a)" role="img" aria-label="Red sports car in a car collection showroom"></div>
    <h3>LOREM IPSUM DOLOR SIT AME</h3>
    <p>Lorem ipsum dolor sit amet consectetur adipiscing elit sed doied eiusmod tempor incididunt ut labore et dolore magna .</p>
    <a>Read More</a>
  </div>
</section>

<section class="section newsletter">
  <div class="abs news-bg" role="img" aria-label="Modern garage building with palm trees in blue tint"></div>
  <div class="abs news-car" role="img" aria-label="Custom purple hot rod with flame paintwork"></div>
  <h2 class="abs">SUBSCRIBE TO OUR NEWSLETTER</h2>
  <p class="abs">Lorem ipsum dolor sit ameted, consectetur adipiscing elit, sed do eiusmod tempor incididunt uted labore eted dolore magna aliqua enim ad minim veniam quisted.</p>
  <div class="abs email-field">Email:</div>
  <a class="abs pill submit">SUBMIT <span class="dot-arrow"></span></a>
</section>

<section class="section blog">
  <h2 class="section-title" style="top:76px">OUR BLOG</h2>
  <article class="abs feature">
    <div class="photo-fill" style="background:linear-gradient(180deg,#6a4a34,#9a8066 40%,#e2c22a 68%,#3a3a3c)" role="img" aria-label="Yellow classic car in a garage full of memorabilia"></div>
    <div class="meta" style="margin:16px 0 0 21px"><span><i></i>Share</span><span><i></i>Comments</span><span style="margin-left:16px"><i></i>11.5.2022</span></div>
    <div class="post-title" style="margin:8px 21px 0">LOREM IPSUM DOLOR&nbsp; CONSECTUR LOREM IPSUM ADIPISCING&nbsp; EXERCITATION ULLAMCO LABORIS</div>
    <div class="body" style="margin:8px 21px 0">For businesses with a lot of goods transported, owning a forklift to serve the process of lifting and arranging goods is indispensable.</div>
    <a class="abs pill read">Read More <span class="dot-arrow"></span></a>
  </article>

  <article class="abs mini" style="left:556px;top:151px">
    <div class="photo-fill" style="background:linear-gradient(180deg,#8c8a86,#3a3c3a 60%,#6a6a68)" role="img" aria-label="Dark vintage sedans parked in a hall"></div>
    <div class="meta"><span><i></i>11.5.2022</span></div>
    <div class="post-title">LOREM IPSUM DOLOR&nbsp; CONSECTUR ADIPISCING NOST EXERCITATION</div>
  </article>
  <article class="abs mini" style="left:833px;top:151px">
    <div class="photo-fill" style="background:linear-gradient(180deg,#5a4a3a,#8c7a5a 40%,#c8202a 70%,#555)" role="img" aria-label="Row of red classic cars in a vaulted garage"></div>
    <div class="meta"><span><i></i>11.5.2022</span></div>
    <div class="post-title">LOREM IPSUM DOLOR&nbsp; CONSECTUR ADIPISCING NOST EXERCITATION</div>
  </article>
  <article class="abs mini" style="left:556px;top:412px">
    <div class="photo-fill" style="background:linear-gradient(180deg,#c8cacc,#b03030 50%,#8a8c90)" role="img" aria-label="Car on a red lift in a workshop"></div>
    <div class="meta"><span><i></i>11.5.2022</span></div>
    <div class="post-title">LOREM IPSUM DOLOR&nbsp; CONSECTUR ADIPISCING NOST EXERCITATION</div>
  </article>
  <article class="abs mini" style="left:826px;top:412px">
    <div class="photo-fill" style="background:linear-gradient(180deg,#e6e8ea,#b4b8bc 50%,#3a3c40)" role="img" aria-label="Dark sports car in a bright white garage"></div>
    <div class="meta"><span><i></i>11.5.2022</span></div>
    <div class="post-title">LOREM IPSUM DOLOR&nbsp; CONSECTUR ADIPISCING NOST EXERCITATION</div>
  </article>
</section>

<footer class="section footer">
  <div class="abs foot-brand"><span class="mark"></span>Summit Carports</div>
  <div class="abs foot-social" aria-label="Social links"><span class="soc"></span><span class="soc"></span><span class="soc"></span><span class="soc"></span></div>

  <div class="abs foot-head" style="left:422px">USEFUL LINKS</div>
  <ul class="abs foot-links" style="left:422px"><li>Home</li><li>About Us</li><li>Services</li><li>How Its&nbsp; Work</li><li>Blog</li><li>Contact us</li></ul>

  <div class="abs foot-head" style="left:672px">OTHERLINKS</div>
  <ul class="abs foot-links" style="left:672px"><li>Service</li><li>FAQ</li><li>Policy</li><li>Privacy</li><li>Team</li><li>Contact</li></ul>

  <div class="abs foot-head" style="left:868px">CONTACT US</div>
  <div class="abs foot-contact" style="top:106px">
    <span class="ico"><svg width="14" height="14" viewBox="0 0 24 24"><path d="M6.6 10.8a15 15 0 0 0 6.6 6.6l2.2-2.2a1 1 0 0 1 1-.25 11.4 11.4 0 0 0 3.6.57 1 1 0 0 1 1 1V20a1 1 0 0 1-1 1A17 17 0 0 1 3 4a1 1 0 0 1 1-1h3.5a1 1 0 0 1 1 1c0 1.25.2 2.45.57 3.57a1 1 0 0 1-.25 1z" fill="#fff"/></svg></span>
    <div><b>Phone Number :</b><span>+ 1 888 888 8888</span></div>
  </div>
  <div class="abs foot-contact" style="top:166px">
    <span class="ico"><svg width="14" height="14" viewBox="0 0 24 24"><rect x="3" y="6" width="18" height="13" rx="2" fill="none" stroke="#fff" stroke-width="2"/><path d="M3 7l9 6 9-6" fill="none" stroke="#fff" stroke-width="2"/></svg></span>
    <div><b>Email:</b><span>hello@summitcarports.com</span></div>
  </div>
  <div class="abs foot-contact" style="top:224px">
    <span class="ico"><svg width="14" height="14" viewBox="0 0 24 24"><path d="M12 2a7 7 0 0 0-7 7c0 5 7 13 7 13s7-8 7-13a7 7 0 0 0-7-7z" fill="#fff"/><circle cx="12" cy="9" r="2.5" fill="#2e2e31"/></svg></span>
    <div><b>Address:</b><span>123, Lpsum dolor sit amet,<br>consectetur adipiscing elit</span></div>
  </div>

  <div class="abs foot-rule"></div>
  <div class="abs copy">© 2022 Copyrights Summit Carports All Rights Reserved.</div>
</footer>

</body>
</html>
```